Business Card: RW Office Partners - Your organised problem solver

Business Name: RW Office Partners
Website: www.rwofficepartners.com.au
Email: marisol@rwofficepartners.com.au
Mobile: 61 482 907 236
Facebook: @rwofficepartners
Instrgram: @rwofficepartners

Brading Colours:
HEX
#986474
#ddccd3
#7a8498
#c9d8e4
#000000
#ffffff

Tag Line: Your organised problem solver

Link to DRAFT website:
https://deskhelpcollective.wixsite.com/rw-office-partners

About Page from the website:
My name is Marisol Wrenfield, and I would love to assist you to become more productive in your day to day and achieve your business and personal goals.
My mission is to give you time, time to work on the important tasks of your business or to be able to spend more time with your family. I will take on the tasks you don’t have time for, don’t know well or simply don’t like to do.
I have an extensive background in Administration, Tender Coordination, Document Control, WHS and Quality Management working primarily in the Construction, Mining and Corporate World.
I am passionate about being organised, having order and making things in your life (and mine) easier! I love to watch something unfold and grow into something amazing! I am known for being the go-to problem solver, the organiser of all things, producing high standards of work even under pressure. I’m also a confident communicator, and I understand that you’re busy running your business.

Target Market(s)

Small to Medium Business who require assistance in their business by a virtual assistant.

Industry/Entity Type

Virtual Assistant

Contact Information for Business Card

Mobile: 61 482 907 236

Font styles to use
Sans Serif

Colors
ffffff

Requirements
Must have
• Branding Colours as outlined.
Contact Details as outlined.
Logo as provided.
Proper contact details - mobile, facebook, instragm, website.
Simple, Elegant, very clean looking.
Should not have
• Note cute with pictures.
Not too girly as still want to market to construction companies.

```html
<!DOCTYPE html>
<html lang="en">
<head>
<meta charset="utf-8">
<title>RW Office Partners – Business Card</title>
<link href="https://fonts.googleapis.com/css2?family=Arimo:wght@400;600&display=swap" rel="stylesheet">
<style>
  :root {
    --slate: #7a8498;
    --slate-band: #80899b;
    --mauve: #986474;
    --ink: #333333;
    --paper: #ffffff;
  }
  * { margin: 0; padding: 0; box-sizing: border-box; }
  html, body { width: 1200px; height: 1200px; overflow: hidden; background: var(--paper); }
  .canvas {
    position: relative;
    width: 1200px; height: 1200px;
    border: 1.5px solid var(--ink);
    background: var(--paper);
    font-family: "Arimo", Arial, sans-serif;
  }
  .card {
    position: absolute;
    left: 166px; top: 345px;
    width: 868px; height: 510px;
    border: 1.2px solid var(--ink);
    background: var(--paper);
    overflow: hidden;
  }
  .card-bands { position: absolute; left: 0; top: 0; width: 868px; height: 510px; }
  .brand {
    position: absolute;
    left: 556px; top: 82px;
    display: flex; align-items: center; gap: 12px;
  }
  .brand-square { width: 14px; height: 50px; background: var(--mauve); }
  .brand-name {
    color: var(--mauve);
    font-weight: 600;
    font-size: 27px;
    line-height: 1.02;
    letter-spacing: 1.5px;
    text-transform: uppercase;
  }
  .contacts { position: absolute; left: 0; top: 0; list-style: none; }
  .contact {
    position: absolute;
    left: 45px;
    display: flex; align-items: center;
    color: var(--slate);
    font-size: 20.5px;
    white-space: nowrap;
  }
  .contact-icon {
    width: 40px; height: 40px;
    display: flex; align-items: center; justify-content: center;
    margin-right: 10px;
    flex: none;
  }
  .contact-icon svg { display: block; }
  .contact--web   { top: 78px; }
  .contact--mail  { top: 129px; }
  .contact--phone { top: 178px; font-size: 22px; }
  .contact--phone .contact-icon { height: 52px; }
  .contact--fb    { top: 240px; }
  .contact--ig    { top: 293px; }
  .contact--link  { top: 341px; }
  .social-box {
    width: 34px; height: 34px;
    border: 2.5px solid var(--slate);
    border-radius: 6px;
  }
</style>
</head>
<body>
<div class="canvas">
  <div class="card">
    <svg class="card-bands" viewBox="0 0 868 510" aria-hidden="true">
      <path d="M0 450 H607 C637 450 662 465 671 485 L682 510 H0 Z" fill="var(--slate-band)"/>
      <path d="M682 510 L693 485 C702 465 727 450 758 450 H868 V510 Z" fill="var(--mauve)"/>
    </svg>

    <div class="brand">
      <span class="brand-square"></span>
      <span class="brand-name">RW Office<br>Partners</span>
    </div>

    <ul class="contacts">
      <li class="contact contact--web">
        <span class="contact-icon">
          <svg width="40" height="40" viewBox="0 0 40 40" fill="none" stroke="var(--slate)" stroke-width="1.4">
            <circle cx="20" cy="20" r="18.5"/>
            <ellipse cx="20" cy="20" rx="9.5" ry="18.5"/>
            <line x1="20" y1="1.5" x2="20" y2="38.5"/>
            <line x1="1.5" y1="20" x2="38.5" y2="20"/>
            <path d="M5 9 Q20 15 35 9"/>
            <path d="M5 31 Q20 25 35 31"/>
          </svg>
        </span>
        <span class="contact-text">www.rwofficepartners.com.au</span>
      </li>
      <li class="contact contact--mail">
        <span class="contact-icon">
          <svg width="36" height="28" viewBox="0 0 36 28" fill="none" stroke="var(--slate)" stroke-width="2">
            <rect x="1" y="1" width="34" height="26"/>
            <path d="M1 1 L18 16 L35 1"/>
            <path d="M1 27 L13 12 M35 27 L23 12"/>
          </svg>
        </span>
        <span class="contact-text">marisol@rwofficepartners.com.au</span>
      </li>
      <li class="contact contact--phone">
        <span class="contact-icon">
          <svg width="30" height="52" viewBox="0 0 30 52" fill="none" stroke="var(--slate)">
            <rect x="1.5" y="1.5" width="27" height="49" rx="2.5" stroke-width="3"/>
            <line x1="4" y1="6.5" x2="26" y2="6.5" stroke-width="2"/>
            <line x1="4" y1="44" x2="26" y2="44" stroke-width="2"/>
            <line x1="11" y1="4" x2="19" y2="4" stroke-width="1"/>
            <circle cx="15" cy="47" r="1.2" fill="var(--slate)" stroke="none"/>
          </svg>
        </span>
        <span class="contact-text">61 482 907 236</span>
      </li>
      <li class="contact contact--fb">
        <span class="contact-icon"><span class="social-box"></span></span>
        <span class="contact-text">@rwofficepartners</span>
      </li>
      <li class="contact contact--ig">
        <span class="contact-icon"><span class="social-box"></span></span>
        <span class="contact-text">@rwofficepartners</span>
      </li>
      <li class="contact contact--link">
        <span class="contact-icon">
          <svg width="36" height="36" viewBox="0 0 36 36" fill="none" stroke="var(--slate)" stroke-width="4" stroke-linecap="round">
            <path d="M17 12 L22 7 a5 5 0 0 1 7 7 L24 19 a5 5 0 0 1 -7 0"/>
            <path d="M19 24 L14 29 a5 5 0 0 1 -7 -7 L12 17 a5 5 0 0 1 7 0"/>
          </svg>
        </span>
        <span class="contact-text">https://deskhelpcollective.sitecanvas.net/rw-office-partners</span>
      </li>
    </ul>
  </div>
</div>
</body>
</html>
```